Advertising company unique advertising platform

we need a logo design for a new company based in Australia Melbourne. We develop innovated advertising platform where consumer can use this platform to get regular discount, as business owner they can use this platform for free advertisement. Payment for this advertisement platform only payable every two weeks, when I generate revenue for their business

Industry/Entity Type

Advertising

Contact Information for Business Card

Dale Morven | Co-Founder |Managing Director
Suite 718 240 Wattlebrook Lane Melbourne Vic 3000

ABN 38 614 207 923
Tel: +61 0487 259 318 | Email: dale.morven@plivorantu.com

Font styles to use
Decorative
Script

Requirements
Must have
• Try few different design and some round corner business card
Should not have
• One round corner business card...try 4 different colour background not only black, make sure two side is designed. Be creative so imagine you are giving this to a client make sure has wow factor, if you can also try one design with engrave like all the logo, words look 3d feel
• The word Advertising Platform use attached file font

```html
<!DOCTYPE html>
<html lang="en">
<head>
<meta charset="utf-8">
<title>Plivo Rantu – Business Card</title>
<link rel="stylesheet" href="https://fonts.googleapis.com/css2?family=PT+Sans:wght@400;700&display=swap">
<style>
  :root {
    --backdrop: #ece9e4;
    --teal: #1fe6b4;
    --violet: #7f9be0;
    --sky: #1cc6f2;
    --stripe: #19c3ef;
    --charcoal: #2b2b2b;
    --ink: #111111;
    --flame-light: #f3c64c;
    --flame-mid: #ea8f36;
    --flame-deep: #df4a2c;
    --white: #ffffff;
  }
  * { margin: 0; padding: 0; box-sizing: border-box; }
  html, body { width: 1200px; height: 960px; overflow: hidden; }
  body {
    background: var(--backdrop);
    font-family: "PT Sans", sans-serif;
    position: relative;
  }
  .card {
    position: absolute;
    width: 600px;
    height: 344px;
    border-radius: 22px;
    overflow: hidden;
  }
  .card--front { left: 313px; top: 113px; background: var(--charcoal); }
  .card--back {
    left: 311px; top: 472px;
    background: radial-gradient(ellipse 62% 75% at 50% 40%, var(--flame-light) 0%, var(--flame-mid) 50%, var(--flame-deep) 100%);
  }
  .front-art { position: absolute; inset: 0; }
  .contact {
    position: absolute;
    left: 27px; top: 54px;
    color: var(--ink);
    font-size: 15px;
    line-height: 20px;
  }
  .contact__name { font-weight: 700; font-size: 17px; text-transform: uppercase; }
  .contact__role { font-size: 17px; line-height: 21px; text-transform: uppercase; }
  .contact__block { margin-top: 20px; }
  .contact__block + .contact__block { margin-top: 3px; }
  .brand {
    position: absolute;
    display: flex;
    align-items: center;
    gap: 12px;
    font-weight: 700;
    white-space: nowrap;
  }
  .brand__dot { border-radius: 50%; flex: none; }
  .brand--front { left: 335px; top: 232px; font-size: 30px; color: var(--flame-mid); }
  .brand--front .brand__dot { width: 26px; height: 26px; background: var(--flame-mid); }
  .brand--back { left: 0; right: 0; top: 146px; justify-content: center; font-size: 46px; color: var(--white); }
  .brand--back .brand__dot { width: 36px; height: 36px; background: var(--white); }
  .website {
    position: absolute;
    left: 0; right: 0; bottom: 36px;
    text-align: center;
    color: var(--white);
    font-size: 14px;
    letter-spacing: 5px;
  }
</style>
</head>
<body>
  <section class="card card--front">
    <svg class="front-art" width="600" height="344" viewBox="0 0 600 344" aria-hidden="true">
      <defs>
        <linearGradient id="panelGradient" x1="0" y1="0" x2="1" y2="0.3">
          <stop offset="0" stop-color="var(--teal)"/>
          <stop offset="0.5" stop-color="var(--violet)"/>
          <stop offset="1" stop-color="var(--sky)"/>
        </linearGradient>
      </defs>
      <path d="M0,0 H302 C342,22 332,120 302,200 C286,250 280,310 298,344 H0 Z" fill="url(#panelGradient)"/>
      <path d="M318,0 C350,26 344,122 314,206 C299,252 294,310 306,344" fill="none" stroke="var(--stripe)" stroke-width="5"/>
    </svg>
    <div class="contact">
      <p class="contact__name">Dale Morven</p>
      <p class="contact__role">Co-Founder</p>
      <p class="contact__role">Managing Director</p>
      <div class="contact__block">
        <p>Plivo Rantu</p>
        <p>ABN 38 614 207 923</p>
      </div>
      <div class="contact__block">
        <p>Suite 718 240</p>
        <p>Wattlebrook Lane</p>
        <p>Melbourne Vic 3000</p>
      </div>
      <div class="contact__block">
        <p>P : +61 0487 259 318</p>
        <p>dale.morven@plivorantu.com</p>
      </div>
    </div>
    <div class="brand brand--front"><span class="brand__dot"></span>Brightwell Hub</div>
  </section>

  <section class="card card--back">
    <div class="brand brand--back"><span class="brand__dot"></span>Brightwell Hub</div>
    <p class="website">www.plivorantu.com</p>
  </section>
</body>
</html>
```